New Mechanical Maintenance business needs website

New Mechanical Maintenance business in Perth Western Australia needs a nice and easy to navigate website. Showing what we do and how we can be the right fit for other small to medium size business by offering personalized service from our highly skilled team. We deal with both fixed plant repairs like food and chemical processing facilities to heavy equipment like drill rigs, Large boats and earthmoving equipment.

Target Market(s)

Small to medium business to offer personalized services/packages

Industry/Entity Type

e deal with both fixed plant repairs like food and chemical processing facilities to heavy equipment like drill rigs, Large boats and earthmoving equipment.

Coding

Coded - Design and coding required

Number of Pages Required

4 page

Font styles to use
Serif

Colors
0054AA
0677BA
7BADD7
CADEEF
E8F1F8

Requirements
Must have
• A website that is easy to navigate but covers off on the range of services/maintenance we can provide

```html
<!DOCTYPE html>
<html lang="en">
<head>
<meta charset="utf-8">
<title>KVR Maintenance</title>
<link href="https://fonts.googleapis.com/css2?family=Lato:wght@400;700&family=Poppins:wght@500;600;700&display=swap" rel="stylesheet">
<style>
:root{
  --ink:#1d1d1d;
  --slate:#4b5c80;
  --btn:#5a6270;
  --btn-dark:#545c69;
  --band:#efefef;
  --white:#ffffff;
  --footer:#000000;
  --topbar:#6c6c6c;
}
*{margin:0;padding:0;box-sizing:border-box}
html,body{width:1200px;height:3087px;overflow:hidden}
body{position:relative;background:var(--white);font-family:'Lato',sans-serif;color:var(--ink)}
.abs{position:absolute}
.head{font-family:'Poppins',sans-serif;font-weight:600;color:var(--slate);letter-spacing:.3px}

.topbar{left:0;top:0;width:1200px;height:51px;background:var(--topbar);color:#fff;font-size:16px;font-weight:700;display:flex;align-items:center;justify-content:center}
.hero{left:0;top:51px;width:1200px;height:633px;background:linear-gradient(100deg,#141414 0%,#262626 35%,#5a4a3c 60%,#7a6a5a 75%,#3a4258 100%)}
.brand{display:flex;align-items:center;gap:10px;color:#fff;font-family:'Poppins',sans-serif;font-weight:600;font-size:18px}
.brand-dot{width:34px;height:34px;border-radius:50%;border:3px solid #fff}
.nav a{position:absolute;top:118px;color:#fff;font-family:'Poppins',sans-serif;font-weight:600;font-size:15px;text-decoration:none}
.social-dot{position:absolute;width:14px;height:14px;border-radius:50%;background:#fff}
.contact-btn{left:990px;top:106px;width:147px;height:43px;border-radius:22px;background:#fff;color:#333;font-family:'Poppins',sans-serif;font-weight:600;font-size:15px;display:flex;align-items:center;justify-content:center}
.eyebrow{left:112px;top:272px;color:#fff;font-family:'Poppins',sans-serif;font-weight:700;font-size:16px;letter-spacing:4px}
.hero-title{left:108px;top:304px;color:#fff;font-family:'Poppins',sans-serif;font-weight:700;font-size:36px;line-height:51px}
.hero-text{left:112px;top:418px;width:430px;color:#fff;font-size:16px;line-height:31px}
.pill{border-radius:26px;display:flex;align-items:center;justify-content:center;font-family:'Poppins',sans-serif;font-weight:600;font-size:16px}
.hero-cta{left:112px;top:532px;width:164px;height:46px;background:#fff;color:#555}
.hero-tel{left:314px;top:538px;color:#fff;font-family:'Poppins',sans-serif;font-weight:600;font-size:28px}

.origin-visual{left:112px;top:752px;width:473px;height:380px;border-radius:50% 0 0 50%/50% 0 0 50%;background:linear-gradient(160deg,#c9a3c8 0%,#e5b0a0 30%,#6a7d98 60%,#3c4b66 100%);display:flex;align-items:center;justify-content:center}
.origin-name{color:#fff;font-family:'Poppins',sans-serif;font-weight:600;font-size:40px;letter-spacing:3px}
.body-text{font-size:16px;line-height:29px;text-align:justify}
.dark-btn{background:var(--btn);color:#fff}

.services{left:0;top:1202px;width:1200px;height:653px;background:var(--band)}
.card{position:absolute;top:1333px;width:300px;height:435px;background:#fff;border-radius:150px 150px 0 0;text-align:center}
.card-photo{position:absolute;left:19px;top:22px;width:262px;height:262px;border-radius:50%}
.card h3{position:absolute;left:0;width:100%;top:306px;font-family:'Poppins',sans-serif;font-weight:600;font-size:21px;line-height:29px;color:var(--slate)}
.card p{position:absolute;left:20px;width:260px;font-size:14px;line-height:26px}
.arrow{position:absolute;top:1537px;width:28px;height:28px;border-radius:50%;background:#000}

.why-visual{left:627px;top:1928px;width:573px;height:378px;border-radius:230px 0 0 190px/190px 0 0 190px;background:linear-gradient(120deg,#8a8f97 0%,#b73a3a 35%,#5b6a88 60%,#2c3440 100%)}
.news-form{left:255px;top:2542px;width:690px;height:60px;border-radius:30px;background:#fff;box-shadow:0 3px 12px rgba(0,0,0,.14);overflow:hidden}
.news-input{position:absolute;left:24px;top:0;line-height:60px;font-size:16px;font-weight:700;color:#333}
.news-btn{position:absolute;right:0;top:0;width:208px;height:60px;background:var(--btn-dark);color:#fff;font-family:'Poppins',sans-serif;font-weight:600;font-size:20px;display:flex;align-items:center;justify-content:center}

.footer{left:0;top:2686px;width:1200px;height:401px;background:var(--footer);color:#fff}
.foot-social{position:absolute;top:2914px;width:32px;height:32px;border-radius:50%;background:#fff}
.foot-head{position:absolute;top:2760px;font-family:'Poppins',sans-serif;font-weight:600;font-size:18px;color:#fff}
.foot-link{position:absolute;font-size:15px;color:#fff;display:flex;align-items:center;gap:8px}
.contact-ico{position:absolute;left:863px;width:32px;height:32px;border-radius:50%;background:#fff;display:flex;align-items:center;justify-content:center}
.rule{left:112px;top:3008px;width:977px;height:1px;background:#bbb}
.copy{left:0;top:3041px;width:1200px;text-align:center;font-family:'Poppins',sans-serif;font-weight:600;font-size:17px;color:#fff}
</style>
</head>
<body>

<div class="abs topbar">Call us today on +1 555 010 0199 for a free onsite quotation or email hello@kvrmaintenance.example</div>

<header class="abs hero" role="img" aria-label="Technician with laptop inspecting a jet engine"></header>
<div class="abs brand" style="left:64px;top:110px"><span class="brand-dot"></span>KVR MAINTENANCE</div>
<nav class="nav">
  <a style="left:294px">HOME</a>
  <a style="left:387px">ABOUT</a>
  <a style="left:488px">WHAT WE DO</a>
  <a style="left:637px">WHY CHOOSE US</a>
</nav>
<span class="social-dot" style="left:815px;top:120px"></span>
<span class="social-dot" style="left:856px;top:120px"></span>
<span class="social-dot" style="left:895px;top:120px"></span>
<span class="social-dot" style="left:936px;top:120px"></span>
<div class="abs contact-btn">CONTACT US</div>

<div class="abs eyebrow">WELCOME TO KVR MAINTENANCE</div>
<h1 class="abs hero-title">MECHANICAL MAINTENANCE<br>BUSINESS</h1>
<p class="abs hero-text">Director of the company has over 20-year experience in the fixed and mobile plant industries ranging from Perth local and overseas.</p>
<div class="abs pill hero-cta">GET STARTED</div>
<div class="abs hero-tel">TEL: +1 555 010 0199</div>

<section>
  <div class="abs origin-visual" role="img" aria-label="City skyline at dusk behind the company name"><span class="origin-name">KVR MAINTENANCE</span></div>
  <h2 class="abs head" style="left:661px;top:738px;font-size:32px">WHERE WE COME FROM</h2>
  <p class="abs body-text" style="left:661px;top:790px;width:428px">Director of the company has over 20-year experience in the fixed and mobile plant industries ranging from Perth local and overseas. Facilities like precious metals refining, offshore drilling and production platform, open cut and underground mining, civils, geotechnical and construction equipment and large-scale construction as an expat overseas.</p>
  <p class="abs body-text" style="left:661px;top:993px;width:428px">We offer personalised service to all small and medium size business across a diverse range of industries.</p>
  <div class="abs pill dark-btn" style="left:661px;top:1072px;width:157px;height:47px">READ MORE</div>
</section>

<section>
  <div class="abs services"></div>
  <h2 class="abs head" style="left:0;width:1200px;text-align:center;top:1257px;font-size:32px">WHAT WE DO</h2>
  <span class="arrow" style="left:43px"><svg width="28" height="28" viewBox="0 0 28 28"><path d="M16 8l-6 6 6 6" stroke="#fff" stroke-width="2.5" fill="none"/></svg></span>
  <span class="arrow" style="left:1143px"><svg width="28" height="28" viewBox="0 0 28 28"><path d="M12 8l6 6-6 6" stroke="#fff" stroke-width="2.5" fill="none"/></svg></span>

  <article class="card" style="left:112px">
    <div class="card-photo" role="img" aria-label="Drill rig at sunset" style="background:linear-gradient(160deg,#d9a56a,#6b4a2e 60%,#3a2a1c)"></div>
    <h3>DRILL RIGS</h3>
    <p style="top:340px">Temporibus autem quibusdam et aut officiis debitis aut rerum necessitat ibus saepe evenie.</p>
  </article>
  <article class="card" style="left:451px">
    <div class="card-photo" role="img" aria-label="Engine room of a large boat" style="background:linear-gradient(160deg,#e6e6e6,#8a8a8a 55%,#2a2a2a)"></div>
    <h3>LARGE BOATS</h3>
    <p style="top:340px">Emporibus autem quibusdam et aut officiis debitis aut rerum necessitat ibus saepe evenie.</p>
  </article>
  <article class="card" style="left:789px">
    <div class="card-photo" role="img" aria-label="Excavator on a construction site" style="background:linear-gradient(170deg,#6f8fae,#c77a3a 55%,#4a3a2c)"></div>
    <h3>EARTHMOVING<br>EQUIPMENT</h3>
    <p style="top:369px">Officiis debitis aut rerum necessitat ibus saepe evenie.</p>
  </article>
</section>

<section>
  <h2 class="abs head" style="left:112px;top:1921px;font-size:32px">WHY CHOOSE US</h2>
  <p class="abs body-text" style="left:112px;top:1973px;width:428px">Nam libero tempore, cum soluta nobis est eligendi optio cumque nihil impedit quo minus id quod maxime placeat facere possimus, omnis voluptas assumenda est, omnis dolor repellendus. Temporibus autem qnecessitatibus saepe eveniet ut et voluptates repudiandae sint et molestiae non recusandae.</p>
  <p class="abs body-text" style="left:112px;top:2148px;width:428px">Itaque earum rerum hic tenetur a sapiente delectus, ut aut reiciendis voluptatibus maiores alias consequatur aut perferendis doloribus asperiores repellat.</p>
  <div class="abs pill dark-btn" style="left:112px;top:2256px;width:157px;height:46px">READ MORE</div>
  <div class="abs why-visual" role="img" aria-label="Technician with tablet checking valves and pressure gauges"></div>
</section>

<section>
  <h2 class="abs head" style="left:0;width:1200px;text-align:center;top:2387px;font-size:32px">SIGN UP OUR NEWSLETTER</h2>
  <p class="abs" style="left:190px;top:2451px;width:820px;text-align:center;font-size:15px;line-height:27px">Nemo enim ipsam voluptatem quia voluptas sit aspernatur aut odit aut fugit, sed quia consequuntur magni dolores eos qui ratione voluptatem sequi nesciunt.</p>
  <div class="abs news-form">
    <span class="news-input">Enter the Mail</span>
    <span class="news-btn">SUBSCRIBE</span>
  </div>
</section>

<footer>
  <div class="abs footer"></div>
  <div class="abs brand" style="left:112px;top:2800px;font-size:20px"><span class="brand-dot" style="width:40px;height:40px"></span>KVR MAINTENANCE</div>
  <span class="foot-social" style="left:111px"></span>
  <span class="foot-social" style="left:169px"></span>
  <span class="foot-social" style="left:226px"></span>
  <span class="foot-social" style="left:284px"></span>

  <div class="foot-head" style="left:430px">QUICK LINKS</div>
  <div class="foot-link" style="left:430px;top:2804px"><svg width="14" height="12" viewBox="0 0 14 12"><path d="M0 6h11M7 1l5 5-5 5" stroke="#fff" stroke-width="2.2" fill="none"/></svg>Home</div>
  <div class="foot-link" style="left:430px;top:2838px"><svg width="14" height="12" viewBox="0 0 14 12"><path d="M0 6h11M7 1l5 5-5 5" stroke="#fff" stroke-width="2.2" fill="none"/></svg>About</div>
  <div class="foot-link" style="left:430px;top:2872px"><svg width="14" height="12" viewBox="0 0 14 12"><path d="M0 6h11M7 1l5 5-5 5" stroke="#fff" stroke-width="2.2" fill="none"/></svg>Services</div>
  <div class="foot-link" style="left:430px;top:2906px"><svg width="14" height="12" viewBox="0 0 14 12"><path d="M0 6h11M7 1l5 5-5 5" stroke="#fff" stroke-width="2.2" fill="none"/></svg>Testimonials</div>
  <div class="foot-link" style="left:430px;top:2941px"><svg width="14" height="12" viewBox="0 0 14 12"><path d="M0 6h11M7 1l5 5-5 5" stroke="#fff" stroke-width="2.2" fill="none"/></svg>Contact Us</div>

  <div class="foot-head" style="left:655px">HELP LINKS</div>
  <div class="foot-link" style="left:655px;top:2804px"><svg width="14" height="12" viewBox="0 0 14 12"><path d="M0 6h11M7 1l5 5-5 5" stroke="#fff" stroke-width="2.2" fill="none"/></svg>FAQ</div>
  <div class="foot-link" style="left:655px;top:2838px"><svg width="14" height="12" viewBox="0 0 14 12"><path d="M0 6h11M7 1l5 5-5 5" stroke="#fff" stroke-width="2.2" fill="none"/></svg>Terms of use</div>
  <div class="foot-link" style="left:655px;top:2872px"><svg width="14" height="12" viewBox="0 0 14 12"><path d="M0 6h11M7 1l5 5-5 5" stroke="#fff" stroke-width="2.2" fill="none"/></svg>Privacy Policy</div>
  <div class="foot-link" style="left:655px;top:2906px"><svg width="14" height="12" viewBox="0 0 14 12"><path d="M0 6h11M7 1l5 5-5 5" stroke="#fff" stroke-width="2.2" fill="none"/></svg>Support Links</div>
  <div class="foot-link" style="left:655px;top:2941px"><svg width="14" height="12" viewBox="0 0 14 12"><path d="M0 6h11M7 1l5 5-5 5" stroke="#fff" stroke-width="2.2" fill="none"/></svg>Conditions</div>

  <div class="foot-head" style="left:863px">CONTACT US</div>
  <span class="contact-ico" style="top:2810px"><svg width="14" height="18" viewBox="0 0 14 18"><path d="M7 0a7 7 0 0 0-7 7c0 5 7 11 7 11s7-6 7-11a7 7 0 0 0-7-7z" fill="#000"/><circle cx="7" cy="7" r="2.5" fill="#fff"/></svg></span>
  <div class="foot-link" style="left:907px;top:2804px;display:block;line-height:27px">KVR Maintenance<br>United States</div>
  <span class="contact-ico" style="top:2870px"><svg width="16" height="16" viewBox="0 0 16 16"><path d="M3 1l3 3-2 2c1 2 3 4 5 5l2-2 3 3-2 3C7 15 1 9 1 3z" fill="#000"/></svg></span>
  <div class="foot-link" style="left:906px;top:2876px">+1 555 010 0199</div>
  <span class="contact-ico" style="top:2921px"><svg width="16" height="12" viewBox="0 0 16 12"><rect width="16" height="12" rx="1.5" fill="#000"/><path d="M1 1l7 6 7-6" stroke="#fff" stroke-width="1.5" fill="none"/></svg></span>
  <div class="foot-link" style="left:906px;top:2927px">hello@kvrmaintenance.example</div>

  <div class="abs rule"></div>
  <div class="abs copy">Copyrights@2024. KVR Maintenance.All Rights Reserved</div>
</footer>

</body>
</html>
```